Business Card Design - Amberfield Court

We are looking at a new design for our business cards that has a modern and professional look. We run a residential aged care facility focussing on the care of residents. The cards will be used for potential clients, consultants and business opportunities in this sector. Blue and white is our main colours and would to see these colours incorporated in the design.
Industry/Entity Type
Business
Contact Information for Business Card
Amberfield Court, Darren Walsh, dwalsh@amberfieldcourt.com.au, Finance Manager, 0472 639 208, BCom, 37 Marrabel Crescent, Brindle Vale, Qld 4093.
Look and feel
Each slider illustrates characteristics of the customer's brand and the style your logo design should communicate.

```html
<!DOCTYPE html>
<html lang="en">
<head>
<meta charset="utf-8">
<title>Amberfield Court – Business Card</title>
<link rel="stylesheet" href="https://fonts.googleapis.com/css2?family=Open+Sans:ital,wght@0,300;0,400;0,600;0,700;1,400&display=swap">
<style>
  :root {
    --canvas: #eceff1;
    --card-white: #ffffff;
    --brand-blue: #5b98b0;
    --brand-blue-deep: #3f7d96;
    --brand-blue-light: #86bbcf;
    --name-blue: #6ea6bc;
    --text-grey: #4e5659;
    --mist: #dfe8ed;
    --on-blue: #e9f3f7;
    --on-blue-dim: #2f5f73;
  }
  * { box-sizing: border-box; margin: 0; padding: 0; }
  html, body {
    width: 1200px; height: 1023px; overflow: hidden;
    background: var(--canvas);
    font-family: "Open Sans", Arial, sans-serif;
  }
  .sheet {
    position: relative; width: 1200px; height: 1023px;
    display: flex; align-items: center; justify-content: center; gap: 40px;
  }
  .card {
    position: relative; width: 540px; height: 330px; overflow: hidden;
    box-shadow: 0 4px 18px rgba(0,0,0,.12);
  }

  /* Front */
  .card--front { background: var(--card-white); }
  .front__figures {
    position: absolute; left: 0; bottom: 0; width: 330px; height: 210px;
    background: radial-gradient(ellipse at 45% 70%, var(--mist) 0%, rgba(223,232,237,.6) 55%, rgba(255,255,255,0) 80%);
  }
  .brand-mark {
    position: absolute; top: 34px; right: 30px;
    display: flex; align-items: center; gap: 10px;
  }
  .brand-mark__dot {
    width: 36px; height: 36px; border-radius: 50%; background: var(--brand-blue);
  }
  .brand-mark__name {
    font-size: 17px; font-weight: 400; letter-spacing: 2px; text-transform: uppercase;
    color: var(--brand-blue);
  }
  .front__rule {
    position: absolute; left: 36px; right: 30px; top: 150px;
    height: 1px; background: var(--name-blue);
  }
  .front__address {
    position: absolute; right: 30px; top: 166px; text-align: right;
    font-size: 12px; line-height: 19px; letter-spacing: .4px;
    text-transform: uppercase; color: var(--text-grey);
  }
  .contact {
    position: absolute; left: 36px; bottom: 30px;
  }
  .contact__name {
    font-size: 22px; font-weight: 700; letter-spacing: 1px; text-transform: uppercase;
    color: var(--name-blue); line-height: 1.1;
  }
  .contact__role {
    font-size: 12px; letter-spacing: .5px; text-transform: uppercase;
    color: var(--text-grey); margin: 4px 0 12px;
  }
  .contact__line {
    display: flex; align-items: center; gap: 7px;
    font-size: 12px; color: var(--text-grey); line-height: 20px;
  }
  .contact__icon { width: 12px; height: 12px; flex: none; }

  /* Back */
  .card--back {
    background: linear-gradient(120deg, var(--brand-blue-deep) 0%, var(--brand-blue) 55%, var(--brand-blue-light) 100%);
  }
  .back__figures {
    position: absolute; right: 0; bottom: 0; width: 360px; height: 190px;
    background: radial-gradient(ellipse at 55% 75%, rgba(47,95,115,.45) 0%, rgba(47,95,115,.2) 50%, rgba(47,95,115,0) 78%);
  }
  .back__title {
    position: absolute; left: 36px; top: 40px;
    font-size: 30px; font-weight: 300; letter-spacing: 4px; text-transform: uppercase;
    color: var(--on-blue-dim);
  }
  .back__tagline {
    position: absolute; left: 36px; top: 88px;
    font-size: 17px; font-style: italic; letter-spacing: 1px;
    color: var(--on-blue);
  }
</style>
</head>
<body>
<main class="sheet">
  <section class="card card--front" aria-label="Business card front">
    <div class="front__figures" role="img" aria-label="Faint illustration of a carer supporting an elderly resident"></div>
    <div class="brand-mark">
      <span class="brand-mark__dot"></span>
      <span class="brand-mark__name">Amberfield Court</span>
    </div>
    <div class="front__rule"></div>
    <p class="front__address">BCom, 37 Marrabel Crescent<br>Brindle Vale, Qld 4093.</p>
    <div class="contact">
      <h1 class="contact__name">Darren Walsh</h1>
      <p class="contact__role">Finance Manager</p>
      <p class="contact__line">
        <svg class="contact__icon" viewBox="0 0 12 12" aria-hidden="true">
          <rect width="12" height="12" rx="2" fill="#6ea6bc"/>
          <rect x="4" y="2" width="4" height="8" rx="1" fill="#fff"/>
        </svg>
        0472 639 208
      </p>
      <p class="contact__line">
        <svg class="contact__icon" viewBox="0 0 12 12" aria-hidden="true">
          <rect width="12" height="12" rx="2" fill="#6ea6bc"/>
          <rect x="2.5" y="3.5" width="7" height="5" fill="#fff"/>
          <path d="M2.5 3.5 L6 6.5 L9.5 3.5" fill="none" stroke="#6ea6bc" stroke-width=".8"/>
        </svg>
        dwalsh@amberfieldcourt.com.au
      </p>
    </div>
  </section>

  <section class="card card--back" aria-label="Business card back">
    <div class="back__figures" role="img" aria-label="Faint illustration of a carer supporting an elderly resident"></div>
    <h2 class="back__title">Amberfield Court</h2>
    <p class="back__tagline">Quality, Dignity, Individuality</p>
  </section>
</main>
</body>
</html>
```